Wine Bottle Label Logo Design

My fiancé and I are getting married in September and we made homemade wine which will be given to the guests as a wedding favor. We need label/logo for our wine bottles. We were looking for something rustic yet modern and simple. We had an idea for beige and cranberry colored wine stained, weathered, imperfect heart. Things that will need to be incorporated into the label design are as follows:
Our last name and also the name of the wine: Carudi
The year: 2012
Where is says Alcohol Content on a wine bottle normally write: Alcohol: Deceiving% by vol.
Type of wine: Red Wine
Incorporate our wedding date: Foot Stomped and Bottled for Marla and Ned's Wedding Day 9/28/13

```html
<!DOCTYPE html>
<html lang="en">
<head>
<meta charset="utf-8">
<title>Carudi Red Wine Label</title>
<link rel="stylesheet" href="https://fonts.googleapis.com/css2?family=Cedarville+Cursive&display=swap">
<style>
  :root {
    --wood-light: #c2bcb3;
    --wood-mid: #aaa39a;
    --wood-dark: #8f887f;
    --panel-fill: rgba(255, 255, 255, 0.28);
    --panel-edge: rgba(255, 255, 255, 0.35);
    --ink: #141212;
    --cranberry: #7b4a4c;
  }
  html, body {
    margin: 0;
    padding: 0;
    overflow: hidden;
  }
  body {
    width: 960px;
    height: 1200px;
  }
  .label {
    position: relative;
    width: 960px;
    height: 1200px;
    overflow: hidden;
    font-family: "Cedarville Cursive", cursive;
    color: var(--ink);
  }
  .wood-backdrop {
    position: absolute;
    inset: 0;
    background:
      repeating-linear-gradient(90deg, rgba(0,0,0,0.04) 0 2px, transparent 2px 38px),
      linear-gradient(90deg, var(--wood-dark) 0%, var(--wood-light) 22%, var(--wood-mid) 48%, var(--wood-light) 72%, var(--wood-dark) 100%);
  }
  .brand {
    position: absolute;
    top: 110px;
    left: 0;
    width: 960px;
    display: flex;
    justify-content: center;
    align-items: center;
    gap: 22px;
  }
  .brand-dot {
    width: 64px;
    height: 64px;
    border-radius: 50%;
    background: var(--cranberry);
  }
  .brand-name {
    font-size: 84px;
    line-height: 1;
    color: var(--cranberry);
  }
  .info-panel {
    position: absolute;
    left: 118px;
    top: 305px;
    width: 744px;
    height: 850px;
    border-radius: 22px;
    background: var(--panel-fill);
    border: 1px solid var(--panel-edge);
    box-sizing: border-box;
    text-align: center;
  }
  .info-panel > * {
    position: absolute;
    left: 0;
    right: 0;
    margin: 0;
    font-weight: normal;
    white-space: nowrap;
  }
  .vintage {
    top: 10px;
    font-size: 56px;
    line-height: 70px;
    letter-spacing: 6px;
  }
  .wine-type {
    top: 126px;
    font-size: 34px;
    line-height: 50px;
    letter-spacing: 3px;
  }
  .tasting-note {
    top: 199px;
    font-size: 37px;
    line-height: 92px;
    letter-spacing: 3px;
  }
  .wedding-note {
    top: 590px;
    font-size: 30px;
    line-height: 52px;
    letter-spacing: 2px;
  }
  .alcohol {
    top: 755px;
    font-size: 35px;
    line-height: 50px;
    letter-spacing: 3px;
  }
</style>
</head>
<body>
  <main class="label">
    <div class="wood-backdrop" role="img" aria-label="Weathered grey barn wood planks"></div>

    <div class="brand">
      <span class="brand-dot"></span>
      <span class="brand-name">carudi</span>
    </div>

    <section class="info-panel">
      <h1 class="vintage">2012</h1>
      <p class="wine-type">Red Wine</p>
      <p class="tasting-note">Aged outdoors during the cold<br>winter months to allow for a slower<br>fermentation process. Its like a<br>warm sweet hug in a bottle.</p>
      <p class="wedding-note">Foot Stomped and Bottled for Marla and Ned's<br>Wedding Day 9/28/13</p>
      <p class="alcohol">Alcohol: Deceiving% by vol.</p>
    </section>
  </main>
</body>
</html>
```